Front and back cover design for skincare marketing materials

Thank you for showing an interest in my project.
Project Details.

I require a front and back cover for our marketing materials.
·       Front Cover size: 105 mm W x 150 mm H.
·       Back Cover size:  105 mm W x 150 mm H.
·       It must include these two colors. You can use a third color if you wish.
1.     #DBA09D
2.     #FFFFFF
 
Front Cover
·      The front cover will have a faded image of the Kakadu Plum branch and fruit. There are two image files, KP_image-1.jpg and kp_image-2.jpeg. You can use both images, just a portion of them, or source alternative royalty-free images of Kakadu Plum that may better fit the design. These two files have been uploaded.
 
The front cover wording.
Top of the front cover.
a.     The title of the image. “Kakadu Plum”
b.     The brand name, “Vellora Skincare”. The file brand_name.ai uploaded.
 
Bottom of the front cover- Designer's choice of font.
The bottom of the front cover contains three lines of text in the following order.  
1.     Australian Native Ingredients
2.     100% Natural · Organic · Wild-harvested
3.     Australian-Made Premium Skincare
 
Back Cover
·      Back Cover wording.The back cover contains the following words "grown by nature" in white (#FFFFFF) of font Italianno (font_file.ttf) with a background color of #DBA09D as seen in the sample box (sample_box.pdf) right-side panel
 
Please provide one file for the front cover and a separate file for the back cover.
All the elements of the files must be editable.
 
Do NOT use the Curve function on the files, as the text must remain editable/changeable.
 
All assets/resources/files, including fonts not supplied by us but used by the designer, must be named and provided with the finished design.
Updates

Slow to provide project details.

Target Market(s)

Beauty-minded Asian consumers between the ages of 32 and 75 who take a proactive approach to maintaining younger-looking skin. Those who already know the danger of skin damage caused by skincare containing harsh chemicals choose effective natural/organic solutions to meet their skincare needs. Those who wish a more radiant glow and youthful appearance to their skin. Usually, a two-income middle to high-income bracket couples with a mindset for health and beauty.

Industry/Entity Type

beauty

Font styles to use
Other font styles liked:
• I will provide a font file and a brand name file.

Requirements
Must have
• You must use the two colors provided on the product box. The designer may use a third color.
Nice to have
• some gold colour

```html
<!DOCTYPE html>
<html lang="en">
<head>
<meta charset="utf-8">
<title>Vellora Skincare – Kakadu Plum Covers</title>
<link href="https://fonts.googleapis.com/css2?family=Italianno&family=Montserrat:wght@500;800&family=Oswald:wght@400&display=swap" rel="stylesheet">
<style>
  :root {
    --stage: #5e3a3a;
    --rose: #dba09d;
    --rose-light: #f3dcdb;
    --white: #ffffff;
    --ink: #222222;
    --slate: #6e6e6e;
    --rule: #c9c9c9;
  }
  * { margin: 0; padding: 0; box-sizing: border-box; }
  html, body { width: 1200px; height: 1200px; overflow: hidden; }
  body {
    background: var(--stage);
    position: relative;
    font-family: "Montserrat", sans-serif;
  }
  .cover {
    position: absolute;
    top: 245px;
    width: 439px;
    height: 626px;
    box-shadow: 0 18px 40px rgba(40, 20, 20, 0.45);
  }
  .cover--front { left: 129px; background: var(--white); }
  .cover--back { left: 647px; background: var(--rose); }

  /* Front: brand */
  .brand {
    position: absolute;
    top: 70px;
    left: 0;
    width: 100%;
    text-align: center;
    color: var(--rose);
    font-family: "Montserrat", sans-serif;
    font-weight: 500;
    font-size: 22px;
    letter-spacing: 7px;
    line-height: 1.6;
    text-transform: uppercase;
  }

  /* Front: feature panel */
  .feature {
    position: absolute;
    left: 75px;
    top: 179px;
    width: 267px;
    height: 313px;
    background: radial-gradient(ellipse at 50% 55%, var(--rose-light) 0%, #e8c0be 55%, var(--rose) 100%);
  }
  .feature__frame {
    position: absolute;
    inset: 18px;
    border: 2px solid var(--white);
  }
  .feature__photo {
    position: absolute;
    left: 39px;
    top: 252px;
    width: 379px;
    height: 192px;
    border-radius: 45% 55% 40% 50%;
    background: radial-gradient(ellipse at 45% 50%, #b5b53a 0%, #8f9a2e 40%, rgba(70, 120, 40, 0.55) 70%, rgba(255, 255, 255, 0) 100%);
  }
  .feature__title {
    position: absolute;
    left: 112px;
    width: 192px;
    color: var(--white);
    font-weight: 800;
    text-align: center;
    white-space: nowrap;
  }
  .feature__title--main { top: 232px; font-size: 62px; line-height: 62px; letter-spacing: 1px; }
  .feature__title--sub { top: 357px; font-size: 30px; line-height: 32px; letter-spacing: 9px; padding-left: 9px; }

  /* Front: claims */
  .claims {
    position: absolute;
    top: 545px;
    left: 0;
    width: 100%;
    font-family: "Oswald", sans-serif;
    font-size: 9.5px;
    letter-spacing: 1px;
    text-transform: uppercase;
    text-align: center;
  }
  .claim {
    position: absolute;
    top: 0;
    height: 38px;
    padding-top: 6px;
    border-top: 1px solid var(--rose);
    border-bottom: 1px solid var(--rule);
    line-height: 12px;
    white-space: nowrap;
  }
  .claim__lead { display: block; color: var(--slate); }
  .claim__detail { display: block; color: var(--rose); }
  .claim--native { left: 40px; width: 88px; }
  .claim--natural { left: 161px; width: 119px; }
  .claim--made { left: 314px; width: 84px; }

  /* Back */
  .back__frame {
    position: absolute;
    left: 24px;
    right: 24px;
    top: 27px;
    bottom: 27px;
    border: 1px solid var(--white);
  }
  .tagline {
    position: absolute;
    top: 270px;
    left: 0;
    width: 100%;
    text-align: center;
    color: var(--white);
    font-family: "Italianno", cursive;
    font-size: 74px;
    line-height: 1;
  }

  /* Labels */
  .label {
    position: absolute;
    top: 928px;
    width: 240px;
    text-align: center;
    color: var(--white);
    font-family: "Italianno", cursive;
    font-size: 66px;
    line-height: 1;
  }
  .label--front { left: 228px; }
  .label--back { left: 746px; }
</style>
</head>
<body>
  <section class="cover cover--front">
    <p class="brand">Vellora<br>Skincare</p>
    <div class="feature">
      <div class="feature__frame"></div>
    </div>
    <div class="feature__photo" role="img" aria-label="Kakadu plum fruits with green leaves on a branch"></div>
    <h1 class="feature__title feature__title--main">PLUM</h1>
    <h2 class="feature__title feature__title--sub">KAKADU</h2>
    <div class="claims">
      <p class="claim claim--native"><span class="claim__lead">Australian</span><span class="claim__detail">Native Ingredients</span></p>
      <p class="claim claim--natural"><span class="claim__lead">100% Natural</span><span class="claim__detail">Organic · Wild-harvested</span></p>
      <p class="claim claim--made"><span class="claim__lead">Australian-Made</span><span class="claim__detail">Premium Skincare</span></p>
    </div>
  </section>

  <section class="cover cover--back">
    <div class="back__frame"></div>
    <p class="tagline">grown by nature</p>
  </section>

  <p class="label label--front">Front</p>
  <p class="label label--back">Back</p>
</body>
</html>
```